We need a business card design, letterhead design and envelope design for our corporate image

We are looking for a corporate business card design, letterhead and envelope design to match the business card design. Logo is done.

```html
<!DOCTYPE html>
<html lang="en">
<head>
<meta charset="utf-8">
<title>Kelvane Business Card</title>
<link href="https://fonts.googleapis.com/css2?family=Open+Sans:wght@400;700&display=swap" rel="stylesheet">
<style>
  :root {
    --backdrop: #3a3a3a;
    --card: #1d1d1d;
    --card-deep: #161616;
    --accent: #f5c400;
    --ink: #ffffff;
    --ink-soft: #e6e6e6;
  }
  * { margin: 0; padding: 0; box-sizing: border-box; }
  html, body { width: 1200px; height: 801px; overflow: hidden; }
  body {
    background: var(--backdrop);
    font-family: "Open Sans", Arial, sans-serif;
    display: flex;
    align-items: center;
    justify-content: center;
    gap: 40px;
  }
  .card {
    position: relative;
    width: 520px;
    height: 297px;
    background: var(--card);
    border-bottom: 3px solid var(--accent);
    overflow: hidden;
  }

  /* Front */
  .card-front { display: flex; align-items: center; }
  .brand-name {
    color: var(--ink);
    font-weight: 700;
    font-size: 38px;
    letter-spacing: 0.5px;
    line-height: 1;
    white-space: nowrap;
  }
  .front-logo {
    width: 270px;
    display: flex;
    justify-content: center;
  }
  .divider {
    width: 1px;
    height: 128px;
    background: var(--accent);
  }
  .contact {
    padding-left: 22px;
    color: var(--ink-soft);
    font-size: 12.5px;
    line-height: 1.45;
  }
  .contact-name {
    color: var(--accent);
    font-weight: 700;
    font-size: 17px;
    letter-spacing: 0.3px;
    line-height: 1.2;
  }
  .contact-title { margin-bottom: 10px; }
  .contact-address { margin-bottom: 10px; }
  .contact-line { display: flex; align-items: center; gap: 7px; white-space: nowrap; }
  .contact-line svg { width: 11px; height: 11px; fill: var(--accent); flex: none; }

  /* Back */
  .back-pattern {
    position: absolute;
    inset: 0;
    background: radial-gradient(circle at 70% 40%, #232323 0%, var(--card-deep) 70%);
  }
  .back-logo {
    position: absolute;
    left: 300px;
    top: 150px;
    font-size: 29px;
  }
</style>
</head>
<body>

  <section class="card card-front">
    <div class="front-logo">
      <span class="brand-name">Kelvane</span>
    </div>
    <div class="divider"></div>
    <div class="contact">
      <p class="contact-name">DALE HARWICK</p>
      <p class="contact-title">President</p>
      <p class="contact-address">1180 Harbor Crest Way<br>Bayview CA 92001</p>
      <p class="contact-line">
        <svg viewBox="0 0 24 24"><path d="M6.6 10.8a15 15 0 0 0 6.6 6.6l2.2-2.2a1 1 0 0 1 1-.25 11.4 11.4 0 0 0 3.6.57 1 1 0 0 1 1 1V20a1 1 0 0 1-1 1A17 17 0 0 1 3 4a1 1 0 0 1 1-1h3.5a1 1 0 0 1 1 1c0 1.25.2 2.45.57 3.6a1 1 0 0 1-.25 1z"/></svg>
        555-310-4827
      </p>
      <p class="contact-line">
        <svg viewBox="0 0 24 24"><path d="M2 5h20v14H2z"/><path d="M2 5l10 8 10-8" fill="none" stroke="#1d1d1d" stroke-width="2"/></svg>
        dharwick@kelvane.com
      </p>
      <p class="contact-line">
        <svg viewBox="0 0 24 24"><circle cx="12" cy="12" r="10"/></svg>
        www.kelvane.com
      </p>
    </div>
  </section>

  <section class="card card-back">
    <div class="back-pattern" role="img" aria-label="Embossed repeating pattern in dark tones"></div>
    <span class="brand-name back-logo">Kelvane</span>
  </section>

</body>
</html>
```